Nutritional & Gastrointestinal Health Consulting Service-Website design

We need a website design for a new health consulting service called "Bright Vale" based in Perth, Australia.

We will be providing consulting services in the areas of:
1) Nutrition and Diet
2) Gastrointestinal Health (which means stomach & digestive system related health)

These consulting services will be provided by an Accredited Dietitian and a Paediatric Gastroenterologist.

We are open to creative ideas in terms of design, layout, fonts and colours. We also would love to see images of nature in the backdrop with families (adults with kids) having a good time, fresh fruits and vegetables displayed in a farmer's market or supermarket. 2 or 3 images should be sufficient. We would also definitely want our logo somewhere in the main page of website. The logo file is also attached. Please have a look at a website's design that we really liked. We would love to see designs inspired by that style. The website details are in the in the "nice to have priorities" section of this project brief.

We also would be looking at website designers with software coding skills so that if we like the design we can go ahead with the next step of coding.

The website design should communicate the purpose of the website and at the same time be simple, elegant and unique/eye-catching.

We look forward to receiving creative ideas for our website from you all. Good luck!

More details have been added to our project- for example: Logo, fonts style, must haves etc etc. Please view the updated project brief. Looking forward to receiving your fantastic ideas for our website. Thanking you

Hi, I have updated the colour preference. Will add the content preferences tomorrow. thanks

Hello all, I have now added a LOT more content to what we want in our website. It is very much in detail, so please carefully have a read through the entire project brief. If you have any questions write back to me and I will try to respond as quickly as I can. Last few days were busy so couldn't respond quickly to all of you who had send me designs/queries/questions. Thank you for your patience. I look forward to receiving fantastic designs from you all. Good Luck :-)

Target Market(s)

Adults based in western speaking countries aged 18 to 60 years

Industry/Entity Type

Software

Font styles to use
Sans Serif
Script

Colors
faa54b
acd036

Requirements
Must have
• The website must have the MAIN logo file attached. I have attached 3 files: 1) MAIN logo; 2) supplementary logo A ; 3) supplementary logo B

I have selected 2 colours from the colour scheme (see below)-(as the colour of our logo is that).
However we would also like to see LIGHT CHOCOLATE BROWN or CHOCOLATE BROWN colour used as the background colour of the website
Preferred WEBSITE CONTENT:
1) HOME PAGE:
Content required=
--Company Logo
--Dr Dorian Pelham
Paediatric Gastroenterologist & Hepatologist
-Marla Pelham.
Dietitian & Nutritionist
--Website Menu (either listed horizontally or vertically):
Once clicked on each name:

Under each of the Website Menu items we want the following Headings to be added

2) ABOUT US page:
Sub-heading under this: Qualification, Skills, Special Interest

3) SERVICES
DORIAN'S PAGE: Individual Consultation, Endoscopy procedures
Individual Consultation, Group Based Services, Food Diary, Food & Symptom Diary

4) FEES & REBATE: Content as below:
Please Note: Payment of full fees is required at the time of consultation and procedures. 48 hours notice is required for cancellation of appointments/non-attendance. Failure to provide this may result in a fee being incurred. Please call reception to find out the amount of fee charged for cancellation of appointments/non-attendance.
headings are:
Paediatric Gastroenterology:
Dorian's pge
Individual Consultation - Initial (upto 30 mins):
Review Consultation (upto 15 mins):
Endoscopy procedures - No Gap fees charged. Fees will be billed directly to Vitacover. If any queries, please contact reception.

marla's pge
sub heading:
Individual Consultation - Initial (upto 45 mins):
Individual Consultation - Review (upto 30 mins):

Concession-Individual Consultation -Initial (upto 45 mins):
Concession-Individual Consultation - Review (upto 30 mins):
Please Note: Concession applies for health care card holders & pensioners

Group Based Services: Pricing subject to the type of service provided. Please contact us for an obligation free quote.
Education Topics Include:
- Paediatric Nutrition (Introducing Solids, Fussy Eating, Healthy Eating)
- Pregnancy Nutrition, Gestational Diabetes, Breastfeeding/Lactation Nutrition
- Healthy Eating, Supermarket Shopping Tips, Nutrition Label Reading Tips, Healthier
sub heading under nutrition & diet:
-Vitacover:
--A rebate of $52.95 is available from Vitacover if an EPC ( Enhanced Primary Care)/Chronic Disease Management (CDM) plan is issued by your GP.
--All mandatory paperwork needs to be available at the time of making your appointment for your eligibility.
-Private Health Fund:
--Most private health funds provide rebate on dietetic appointments. However the rebate amount depends on your level of cover. Thus, please contact your health fund to determine your entitled rebate.
-RSB: Approved provider for RSB services

6) FOR DOCTORS: Bright Vale Paediatric Gastroenterologist Referral Form
Bright Vale Dietitian Referral form
7) LOCATIONS & CONTACT

Paediatric Gastroenterology & Hepatology Service
Suite 46
Holy Lantern Bramcote Medical Centre
17 Colin Ferris Pde,
MURDOCH, WA 6150
P: (08) 9422 5061
F: (08) 9422 3094

Nutrition & Diet Service
Suite 46
17 Colin Ferris Pde,
MURDOCH, WA 6150
P: (08) 9422 5061
F: (08) 9422 3094

Tolland Medical Centre
58-60 Karrigan Parkway,
MANDURAH, WA 6210
P: (08) 9647 2283
F: (08) 96724419
www.tmcexample.com.au

This page should have a webform that has following titles:
-Your Name
-Your Email
-Your Phone
-Message

8) NEWS & BLOG
Nice to have
• We liked the design style of the websites below:
https://www.vendoraplex.example/

http://qoravelt.example/

But feel free to use your creativity too
Should not have
• Please do not use any body building or muscle building images

```html
<!DOCTYPE html>
<html lang="en">
<head>
<meta charset="utf-8">
<title>Bright Vale — Paediatric Gastroenterology &amp; Nutrition</title>
<link rel="stylesheet" href="https://fonts.googleapis.com/css2?family=Open+Sans:wght@300;400;700;800&display=swap">
<style>
  :root {
    --brown-deep: #4a2c27;
    --brown-mid: #5a3530;
    --brown-warm: #7a463c;
    --band-left: rgba(44, 26, 24, 0.72);
    --band-right: rgba(58, 36, 32, 0.92);
    --orange: #faa54b;
    --green: #acd036;
    --white: #ffffff;
    --muted: #e6dcd8;
  }
  * { margin: 0; padding: 0; box-sizing: border-box; }
  html, body { width: 1200px; height: 842px; overflow: hidden; }
  body {
    font-family: "Open Sans", Arial, sans-serif;
    background: radial-gradient(ellipse at 95% 10%, var(--brown-warm) 0%, var(--brown-mid) 40%, var(--brown-deep) 75%);
    position: relative;
    color: var(--white);
  }
  .brand-mark {
    position: absolute;
    left: 455px; top: 150px;
    width: 290px; height: 290px;
    border-radius: 50%;
    background: var(--orange);
  }
  .brand-name {
    position: absolute;
    left: 0; width: 1200px; top: 600px;
    text-align: center;
    font-weight: 700;
    color: var(--green);
    font-size: 104px;
    line-height: 1;
  }
  .info-band {
    position: absolute;
    left: 0; top: 368px;
    width: 1200px; height: 123px;
    display: flex;
  }
  .welcome {
    width: 673px;
    background: var(--band-left);
    padding-top: 34px;
    text-align: center;
  }
  .welcome h1 { font-size: 14px; font-weight: 700; letter-spacing: 0.1px; }
  .practitioners { display: flex; margin-top: 3px; }
  .practitioner { flex: 1; font-size: 14px; font-weight: 300; line-height: 21px; }
  .practitioner strong { font-weight: 700; }
  .site-menu {
    flex: 1;
    background: var(--band-right);
    display: flex;
    list-style: none;
    padding-top: 24px;
  }
  .site-menu li {
    flex: 1;
    text-align: center;
    font-size: 10.5px;
    line-height: 14px;
    color: var(--muted);
  }
  .site-menu svg { display: block; margin: 0 auto 6px; height: 24px; }
  .site-menu b { color: var(--white); font-weight: 700; display: block; }
  .site-menu em { font-style: normal; font-weight: 700; }
</style>
</head>
<body>
  <div class="brand-mark" aria-hidden="true"></div>
  <div class="brand-name">Bright Vale</div>

  <section class="info-band">
    <div class="welcome">
      <h1>WELCOME TO COMPREHENSIVE PAEDIATRIC GASTROENTEROLOGY AND HEPATOLOGY SERVICE</h1>
      <div class="practitioners">
        <p class="practitioner"><strong>DR DORIAN</strong> PELHAM<br>Paediatric Gastroenterologist &amp; Hepatologist</p>
        <p class="practitioner"><strong>MARLA</strong> PELHAM<br>Accredited Practising Dietitian</p>
      </div>
    </div>
    <ul class="site-menu">
      <li>
        <svg viewBox="0 0 24 24" width="24"><g fill="var(--orange)"><rect x="1" y="4" width="3" height="3"/><rect x="6" y="4" width="17" height="3"/><rect x="1" y="10" width="3" height="3"/><rect x="6" y="10" width="17" height="3"/><rect x="1" y="16" width="3" height="3"/><rect x="6" y="16" width="17" height="3"/></g></svg>
        <b>ABOUT</b>all about <em>us</em>
      </li>
      <li>
        <svg viewBox="0 0 24 24" width="24"><circle cx="12" cy="13" r="9" fill="var(--orange)"/></svg>
        <b>NUTRITION<br>&amp; DIET</b><em>services</em>
      </li>
      <li>
        <svg viewBox="0 0 24 24" width="24"><circle cx="12" cy="13" r="8" fill="none" stroke="var(--orange)" stroke-width="2.5"/></svg>
        <b>PAEDIATRIC<br>GASTROENTEROLOGY</b><em>services</em>
      </li>
      <li>
        <svg viewBox="0 0 24 24" width="24"><g fill="var(--orange)"><ellipse cx="10" cy="10" rx="9" ry="6"/><path d="M5 14 L3 19 L10 15 Z"/><ellipse cx="16" cy="14" rx="7" ry="5" opacity="0.85"/></g></svg>
        <b>BLOG</b>and <em>News</em>
      </li>
      <li>
        <svg viewBox="0 0 24 24" width="24"><rect x="2" y="5" width="20" height="14" rx="2" fill="none" stroke="var(--orange)" stroke-width="2"/><path d="M2 6 L12 13 L22 6" fill="none" stroke="var(--orange)" stroke-width="2"/></svg>
        <b>CONTACT</b>and <em>Locations</em>
      </li>
    </ul>
  </section>
</body>
</html>
```